July 2022 Industrial Manufacturer Product Expo Mexico City

We manufacture large screws and fastners for large Mining equipment, Trains, large ships, airplanes, wind turbines, and so on. We also do custom work base on the customer needs. No matter the size we can make it.
We have a Expo coming up with companies all over the world. We have to stand out we are a family own business so our customer service will be above and beyond anyone can provide. We do not have a sales force to push our products and services we provide one on one service.
Plus@!! I'm looking for anything that you designers can come up with if it was your company to put on a business card, plus i want to do a 1 or 2 sided pamphlet, and then a website. We make Speciality Bolts for large mining equipment these bolts can be 3 to 4 foot long!!! Plus fasteners, Nuts, washers, any, size, strengths, special materials, we offer more of a ono on one customer service, We are a small company, family own, but can fulfill any type of orders. We can also provide special time lines for emergency orders. "We keep the machines running we here at KRV don't believe in down time" We want to hear any slogan based on our company to stand out.
Thanks i really appreciate all your work and options that we have to pick on. Plus just a thought we could possibly want to entertain a experience Marketing internet help maybe a employment possibility. Thanks

I need 2 cards one in Spanish and English Like the steel back ground maybe send me in some bright red and blue writing Same with the Black cards Please remove the word Military The logo KRV maybe integrate a picture of a Bolt 🔩 Thank you

Still looking for I need 2 cards one in Spanish and English Like the steel back ground maybe send me in some bright red and blue writing Same with the Black cards try bright writing Please remove the word Military The logo KRV maybe integrate a picture of a Bolt 🔩 Plus will need the company to make a brochure and website next Thank you

Target Market(s)

Large Mining, Ship, Train, Green Energy, VELM, and Government equipment. Throughout the World

Industry/Entity Type

We can Custom Manufacture any type of Fastners for Mining equipment, Trains, Ships, Green energy, Governments, or military projects. wind turbines,

Contact Information for Business Card

I attached the name and contact info that's on a card, plus the Company Logo. Would like industrial looking background with Bright Colors that will stand out!! If we can insert somewhere maybe on back that we "Custom Manufacture Any Size or Quantity Fastners for Large Mining Equipment, Trains, Ships, Green Energy Equipment or Government Projects

Font styles to use
Other font styles liked:
• You Pick, has to be bold, colorful standout, Professional looking Beable to read it.

Colors

Designer to choose colors to be used in the design.

Requirements
Must have
• Need in Spanish and English TO STANDOUT FROM THE REST OF THE EXPO!! See Business card details, Rounded corners
Nice to have
• Can i see some of the darker cards with Bright Red and Blue letters I like to see the different type of card material, heavy thickness, plastic, transparent, Metal types, Bright Colors, I saw like Raised letters like on the logo.

```html
<!DOCTYPE html>
<html lang="es">
<head>
<meta charset="utf-8">
<title>KRV – Tarjetas de presentación</title>
<link href="https://fonts.googleapis.com/css2?family=Open+Sans:wght@400;600;700&display=swap" rel="stylesheet">
<style>
  :root {
    --stage: #202020;
    --steel-top: #8a8a8c;
    --steel-mid: #3a3a3c;
    --steel-bottom: #141416;
    --navy: #0a2a8c;
    --blue: #0a7fd0;
    --sky: #1a9ee0;
    --ink: #1b3a8f;
    --grey: #555558;
    --silver: #cfcfd2;
    --paper: #ffffff;
  }
  * { box-sizing: border-box; margin: 0; padding: 0; }
  html, body { width: 1200px; height: 1015px; overflow: hidden; }
  body {
    background: var(--stage);
    font-family: "Open Sans", Arial, sans-serif;
    position: relative;
  }
  .card {
    position: absolute;
    left: 260px;
    width: 680px;
    height: 390px;
    border-radius: 14px;
    overflow: hidden;
  }
  /* Back card */
  .card-back {
    top: 70px;
    background: linear-gradient(180deg, var(--steel-top) 0%, var(--steel-mid) 40%, var(--steel-bottom) 75%);
  }
  .card-back .wordmark {
    position: absolute;
    top: 70px;
    left: 0; right: 0;
    text-align: center;
    font-weight: 700;
    font-size: 110px;
    letter-spacing: 18px;
    color: var(--silver);
  }
  .card-back .tagline-band {
    position: absolute;
    left: 0; right: 0; bottom: 0;
    height: 140px;
    background: linear-gradient(180deg, var(--navy) 0%, var(--blue) 100%);
    display: flex;
    align-items: center;
    justify-content: center;
    text-align: center;
    padding: 0 40px;
  }
  .tagline {
    color: var(--paper);
    font-size: 19px;
    font-weight: 600;
    line-height: 1.3;
  }
  /* Front card */
  .card-front {
    top: 530px;
    background: var(--paper);
  }
  .card-front .wordmark {
    position: absolute;
    top: 150px;
    left: 60px;
    font-weight: 700;
    font-size: 72px;
    letter-spacing: 10px;
    color: var(--grey);
  }
  .divider {
    position: absolute;
    left: 318px;
    top: 70px;
    width: 1px;
    height: 180px;
    background: #b8b8bb;
  }
  .contact {
    position: absolute;
    left: 345px;
    top: 70px;
    right: 24px;
    color: var(--ink);
  }
  .contact .name {
    font-size: 20px;
    font-weight: 700;
    color: var(--blue);
    margin-bottom: 14px;
    white-space: nowrap;
  }
  .contact .line {
    font-size: 15px;
    line-height: 1.35;
  }
  .contact .phones { margin-top: 16px; }
  .phone {
    display: flex;
    align-items: center;
    gap: 8px;
    font-size: 17px;
    line-height: 1.4;
  }
  .phone svg { width: 16px; height: 16px; flex: none; }
  .footer-grey {
    position: absolute;
    left: 0; bottom: 0;
    width: 480px; height: 34px;
    background: linear-gradient(180deg, #8d8d90, #3d3d40);
  }
  .footer-blue {
    position: absolute;
    right: 0; bottom: 0;
    width: 260px; height: 140px;
  }
</style>
</head>
<body>

  <section class="card card-back" aria-label="Reverso de tarjeta">
    <div class="wordmark">KRV</div>
    <div class="tagline-band">
      <p class="tagline">Custom Manufacture Any Size or Quantity Fastners for Large<br>Mining Equipment, Trains, Ships,<br>Green Energy Equipment or Government Projects</p>
    </div>
  </section>

  <section class="card card-front" aria-label="Frente de tarjeta">
    <div class="wordmark">KRV</div>
    <div class="divider"></div>
    <div class="contact">
      <p class="name">Lic.Daniela Marisol Reyes Vega</p>
      <p class="line">Cotizaciones en</p>
      <p class="line">tornilleriakrv.ventas@correo.mx</p>
      <div class="phones">
        <p class="phone">
          <svg viewBox="0 0 16 16" aria-hidden="true"><path d="M3 1.5 L5.5 1.5 L6.5 5 L5 6.2 C5.8 8 7.8 10 9.8 11 L11 9.5 L14.5 10.5 L14.5 13 C14.5 14 13.5 14.7 12.5 14.5 C7 13.5 2.5 9 1.5 3.5 C1.3 2.5 2 1.5 3 1.5 Z" fill="var(--sky)"/></svg>
          5550193601
        </p>
        <p class="phone">
          <svg viewBox="0 0 16 16" aria-hidden="true"><rect x="4" y="1" width="8" height="14" rx="1.5" fill="none" stroke="var(--sky)" stroke-width="1.5"/><line x1="7" y1="12.5" x2="9" y2="12.5" stroke="var(--sky)" stroke-width="1.5"/></svg>
          5550127600
        </p>
      </div>
    </div>
    <div class="footer-grey"></div>
    <svg class="footer-blue" viewBox="0 0 260 140" preserveAspectRatio="none" aria-hidden="true">
      <defs>
        <linearGradient id="band" x1="0" y1="0" x2="0" y2="1">
          <stop offset="0" stop-color="#0a2a8c"/>
          <stop offset="1" stop-color="#0a7fd0"/>
        </linearGradient>
      </defs>
      <polygon points="0,140 10,40 260,0 260,140" fill="url(#band)"/>
    </svg>
  </section>

</body>
</html>
```